Flyer Vacation Gift Certificate

I need to create a beautiful flyer 8.5 x 11 PDF format flyer design. <br/><br/>Instructions:<br/>The flyer will really be a gift voucher for a las vegas vacation getaway. So must have a Las Vegas Theme exciting fun<br/><br/>The voucher should have two modules that will be editable. <br/>Must have a "Compliments Of" area and also must have an "Exclusively For" area<br/><br/>Keep in mind that this flyer will be printed so keep that in mind :)<br/><br/>Here the is the content for the vacation voucher:<br/><br/>There is no doubt that Las Vegas is one of the hottest travel destinations around the world. In fact, some people would even go as far as<br/>saying that perhaps it is THE hottest place to visit. Enjoy up to 4 nights of resort/casino accommodations in exciting Las Vegas, NV. Millions of people travel to this exciting city each year to enjoy its thrills. Thanks to the business you received this certificate from, now you can enjoy exciting Las Vegas, NV too!<br/><br/>Features:<br/>*Travel 7 Days A Week<br/>*Stay Your Choice Of Nights (1-4 Nights)<br/>*Good For Two Adults & Two Children<br/>*Pay Just The Taxes & Fees<br/>*Multiple Travel Date Requests Allowed<br/>*Fully Transferable To Another Person<br/>*Just A 30 Days Advance Notice Required<br/>*You Will Have 12 Months To Complete Travel After Redemption<br/><br/>HOW CAN WE DO THIS?<br/><br/>We contract with the world leading hotel chains and resorts to help them fill their otherwise empty rooms.<br/><br/>We help fill empty rooms which the hotels, resorts and cruise lines turn into additional revenue from other areas of their property and future bookings.<br/><br/>Hotels rarely experience full occupancy, yet they remain open, providing rooms and services at fixed costs. So when hotels give out their rooms by partnering with marketing companies like us, they might miss out on the room fee, but they already didn't have that in the first place, at least now they have the opportunity to gain a customer for their in-house restaurants, room service, their casinos, an extra day stay, future bookings, etc.<br/><br/>VIEW ALL THE DETAILS OF THIS SPECIAL OFFER AND REDEEM ONLINE AT <br/>WWW.QOTAVERNIX.COM<br/><br/>Certificate ID # 47261-38157<br/>Expires 02/29/2020<br/><br/><br/>*terms and conditions apply see website for details<br/><br/>KEEP IN MIND THE EXAMPLES I AM UPLOADING ARE SIMPLY TO SHOW YOU THAT THEY CONTAIN THE "COMPLIMENTS OF" AND "EXCLUSIVELY FOR" ELEMENTS. THESE MUST BE INCLUDED IN NEW DESIGN. PLEASE ONLY USE THE CONTENT I PROVIDED IN BRIEF, DONT USE CONTENT FROM EXAMPLES.

Target Market(s)

CONSUMERS THAT HAVE BEEN REWARDED WITH A VACATION CERTIFICATE FOR DOING BUSINESS WITH A COMPANY.

COMPANIES USE THESE AS MARKETING INCENTIVES TO ATTRACT MORE CUSTOMERS AND TO REWARD LOYALTY, ETC.

Industry/Entity Type

Travel Industry

Colors

Designer to choose colors to be used in the design.

Requirements
Must have
• I need to create a beautiful flyer 8.5 x 11 PDF format flyer design.
• Instructions:
• The flyer will really be a gift voucher for a las vegas vacation getaway. So must have a Las Vegas Theme exciting fun
• The voucher should have two modules that will be editable.
• Must have a "Compliments Of" area and also must have an "Exclusively For" area
• Keep in mind that this flyer will be printed so keep that in mind :)
• Here the is the content for the vacation voucher:
• There is no doubt that Las Vegas is one of the hottest travel destinations around the world. In fact, some people would even go as far as
• saying that perhaps it is THE hottest place to visit. Enjoy up to 4 nights of resort/casino accommodations in exciting Las Vegas, NV. Millions of people travel to this exciting city each year to enjoy its thrills. Thanks to the business you received this certificate from, now you can enjoy exciting Las Vegas, NV too!
• Features:
• *Travel 7 Days A Week
• *Stay Your Choice Of Nights (1-4 Nights)
• *Good For Two Adults & Two Children
• *Pay Just The Taxes & Fees
• *Multiple Travel Date Requests Allowed
• *Fully Transferable To Another Person
• *Just A 30 Days Advance Notice Required
• *You Will Have 12 Months To Complete Travel After Redemption
• HOW CAN WE DO THIS?
• We contract with the world leading hotel chains and resorts to help them fill their otherwise empty rooms.
• We help fill empty rooms which the hotels, resorts and cruise lines turn into additional revenue from other areas of their property and future bookings.
• Hotels rarely experience full occupancy, yet they remain open, providing rooms and services at fixed costs. So when hotels give out their rooms by partnering with marketing companies like us, they might miss out on the room fee, but they already didn't have that in the first place, at least now they have the opportunity to gain a customer for their in-house restaurants, room service, their casinos, an extra day stay, future bookings, etc.
• VIEW ALL THE DETAILS OF THIS SPECIAL OFFER AND REDEEM ONLINE AT
• WWW.QOTAVERNIX.COM
• Certificate ID # 47261-38157
• Expires 02/29/2020
• *terms and conditions apply see website for details
• KEEP IN MIND THE EXAMPLES I AM UPLOADING ARE SIMPLY TO SHOW YOU THAT THEY CONTAIN THE "COMPLIMENTS OF" AND "EXCLUSIVELY FOR" ELEMENTS. THESE MUST BE INCLUDED IN NEW DESIGN. PLEASE ONLY USE THE CONTENT I PROVIDED IN BRIEF, DONT USE CONTENT FROM EXAMPLES.
Nice to have
• EXCITING LAS VEGAS IMAGES THAT MAKE SOMEONE WANT TO GO THERE

```html
<!DOCTYPE html>
<html lang="en">
<head>
<meta charset="utf-8">
<title>Las Vegas Vacation Gift Certificate</title>
<link href="https://fonts.googleapis.com/css2?family=Montserrat:wght@300;400;500;600;700&display=swap" rel="stylesheet">
<style>
  :root {
    --brand-blue: #3d6fa8;
    --brand-blue-dark: #2f5c93;
    --page: #f3f3f3;
    --ink: #4a4a4a;
    --list-ink: #d6e3f1;
    --panel-light: #d9dadd;
    --panel-mid: #b9babd;
    --panel-dark: #5e6065;
    --backdrop: #e9e6e1;
  }
  * { margin: 0; padding: 0; box-sizing: border-box; }
  html, body { width: 1200px; height: 989px; overflow: hidden; background: var(--backdrop); }
  body { font-family: "Montserrat", sans-serif; }

  .flyer {
    position: absolute; left: 270px; top: 24px;
    width: 680px; height: 970px;
    transform: scale(0.97); transform-origin: top left;
    background: var(--page); overflow: hidden;
    box-shadow: 0 2px 10px rgba(0,0,0,.15);
  }
  .hero-photo {
    position: absolute; left: 0; top: 0; width: 680px; height: 270px;
    background:
      linear-gradient(180deg, rgba(0,0,0,0) 55%, rgba(255,170,60,.55) 85%, rgba(40,40,70,.8) 100%),
      linear-gradient(180deg, #3f6fb3 0%, #6f9fd4 40%, #9cb7cf 55%, #5a5f7c 75%, #2b2d45 100%);
  }
  .compliments-card {
    position: absolute; left: 472px; top: 0; width: 188px; height: 178px;
    background: #fff; text-align: center; padding-top: 16px;
  }
  .compliments-card .eyebrow {
    color: var(--brand-blue); font-size: 15px; font-weight: 400; line-height: 18px; letter-spacing: .5px;
  }
  .brand-name {
    display: flex; align-items: center; justify-content: center; gap: 6px;
    margin-top: 6px; color: var(--brand-blue-dark); font-size: 15px; font-weight: 700;
  }
  .brand-name .mark { width: 12px; height: 12px; background: var(--brand-blue-dark); }
  .courtesy { margin-top: 18px; font-size: 12px; color: #222; line-height: 20px; }
  .courtesy .line { font-size: 11.5px; color: #333; }

  .intro-band {
    position: absolute; left: 0; top: 270px; width: 680px; height: 75px;
    background: var(--brand-blue); color: #fff;
    font-size: 9px; line-height: 12px; font-weight: 300; text-align: center;
    padding: 9px 24px 0;
  }

  .section-tab { position: absolute; left: 0; height: 32px; }
  .section-tab svg { position: absolute; left: 0; top: 0; }
  .section-tab h2 {
    position: relative; padding: 8px 0 0 21px;
    color: #fff; font-size: 13px; font-weight: 700; letter-spacing: .4px;
  }
  .tab-how { top: 372px; width: 242px; }
  .tab-terms { top: 566px; width: 242px; }

  .how-copy {
    position: absolute; left: 22px; top: 425px; width: 334px;
    color: var(--ink); font-size: 8.6px; line-height: 11.7px; font-weight: 400;
  }
  .terms-copy {
    position: absolute; left: 21px; top: 618px; width: 330px;
    color: #777; font-size: 6.4px; line-height: 8.7px; text-transform: uppercase;
  }

  .features-panel {
    position: absolute; left: 377px; top: 353px; width: 303px; height: 337px;
    background: var(--brand-blue);
    border-radius: 10px 0 0 70px;
  }
  .features-tab { position: absolute; left: 36px; top: 37px; width: 239px; height: 32px; }
  .features-tab svg { position: absolute; left: 0; top: 0; }
  .features-tab h2 {
    position: relative; padding: 7px 0 0 19px;
    color: var(--brand-blue); font-size: 14px; font-weight: 700;
  }
  .features-list {
    position: absolute; left: 56px; top: 88px; width: 240px;
    color: var(--list-ink); font-size: 9.2px; line-height: 11.7px; font-weight: 400;
    list-style: none;
  }
  .features-list li { position: relative; }
  .features-list li::before {
    content: ""; position: absolute; left: -10px; top: 4px;
    width: 3px; height: 3px; border-radius: 50%; background: var(--list-ink);
  }
  .redeem {
    position: absolute; left: 46px; top: 236px; width: 230px;
    color: var(--list-ink); font-size: 8.8px; line-height: 12px; text-transform: uppercase;
  }
  .redeem-details {
    position: absolute; left: 46px; top: 272px;
    color: #fff; font-size: 9px; line-height: 12px; font-weight: 700;
  }

  .module-compliments {
    position: absolute; left: 0; top: 718px; width: 325px; height: 252px; background: var(--panel-light);
  }
  .module-compliments h3 {
    position: absolute; left: 21px; top: 22px;
    font-size: 11.5px; font-weight: 600; color: #111; letter-spacing: .3px;
  }
  .module-divider { position: absolute; left: 325px; top: 718px; }
  .module-exclusive {
    position: absolute; left: 348px; top: 755px; width: 332px; height: 215px; background: var(--panel-mid);
  }
  .module-exclusive h3 {
    position: absolute; left: 0; right: 0; top: 18px; text-align: center;
    font-size: 12.5px; font-weight: 500; color: #444; letter-spacing: .4px;
  }
</style>
</head>
<body>
<main class="flyer">
  <div class="hero-photo" role="img" aria-label="Las Vegas Strip skyline at dusk with glowing casino resorts and a replica tower"></div>

  <aside class="compliments-card">
    <p class="eyebrow">THIS CERTIFICATE IS<br>COMPLIMENTS OF</p>
    <div class="brand-name"><span class="mark"></span>Nexalo Reach</div>
    <div class="courtesy">
      <p>Certificate Courtesy Of</p>
      <p class="line">Text Line 2</p>
      <p class="line">Text Line 3</p>
    </div>
  </aside>

  <p class="intro-band">There is no doubt that Las Vegas is one of the hottest travel destinations around the world. In fact, some people would even go as far as saying that perhaps it is THE hottest place to visit. Enjoy up to 4 nights of resort/casino accommodations in exciting Las Vegas, NV. Millions of people travel to this exciting city each year to enjoy its thrills. Thanks to the business you received this certificate from, now you can enjoy exciting Las Vegas, NV too!</p>

  <div class="section-tab tab-how">
    <svg width="242" height="32"><polygon points="0,0 230,0 242,16 230,32 0,32" fill="var(--brand-blue)"/></svg>
    <h2>HOW CAN WE DO THIS?</h2>
  </div>
  <p class="how-copy">We contract with the world leading hotel chains and resorts to help them fill their otherwise empty rooms. We help fill empty rooms which the hotels, resorts and cruise lines turn into additional revenue from other areas of their property and future bookings.<br>Hotels rarely experience full occupancy, yet they remain open, providing rooms and services at fixed costs. So when hotels give out their rooms by partnering with marketing companies like us, they might miss out on the room fee, but they already didn't have that in the first place, at least now they have the opportunity to gain a customer for their in-house restaurants, room service, their casinos, an extra day stay, future bookings, etc.</p>

  <div class="section-tab tab-terms">
    <svg width="242" height="32"><polygon points="0,0 230,0 242,16 230,32 0,32" fill="var(--brand-blue)"/></svg>
    <h2>TERMS AND CONDITIONS</h2>
  </div>
  <p class="terms-copy">Keep in mind the examples I am uploading are simply to show you that they contain the "compliments of" and "exclusively for" elements. These must be included in new design. Please only use the content I provided in brief, dont use content from examples.</p>

  <section class="features-panel">
    <div class="features-tab">
      <svg width="239" height="32"><polygon points="0,0 227,0 239,16 227,32 0,32" fill="#fff"/></svg>
      <h2>FEATURES:</h2>
    </div>
    <ul class="features-list">
      <li>Travel 7 Days A Week</li>
      <li>Stay Your Choice Of Nights (1-4 Nights)</li>
      <li>Good For Two Adults &amp; Two Children</li>
      <li>Pay Just The Taxes &amp; Fees</li>
      <li>Multiple Travel Date Requests Allowed</li>
      <li>Fully Transferable To Another Person</li>
      <li>Just A 30 Days Advance Notice Required</li>
      <li>You Will Have 12 Months To Complete Travel After Redemption</li>
    </ul>
    <p class="redeem">View all the details of this special offer and redeem online at</p>
    <p class="redeem-details">WWW.QOTAVERNIX.COM<br>Certificate ID # 47261-38157<br>Expires 02/29/2020</p>
  </section>

  <section class="module-compliments"><h3>COMPLIMENTS OF</h3></section>
  <svg class="module-divider" width="23" height="252"><polygon points="0,0 23,37 23,252 0,252" fill="var(--panel-dark)"/></svg>
  <section class="module-exclusive"><h3>EXCLUSIVELY FOR</h3></section>
</main>
</body>
</html>
```